Summit Ridge Business Card

Side 1: Summit Ridge Logo (logo without Maltese cross) with industrial rope rescue related theme. Our company services - TRAINING - Fire Training, Confined Space Rescue Training, Rope Rescue training, Hazmat Training, Incident Command, EMS, Pump Operations Training. Website - summitridgeexample.com.
Side 2: Summit Ridge Fire Department Logo (logo with Maltese cross) with Firefighter related theme. Company (division) services - FIELD SERVICES - Fire Department, Stand-by Rescue, Safety, EMS, Planning. "Supporting the Emergency Response Community Since 1967"

Add contact information wherever it makes since (Name, Email, Phone).
I would like it to represent the Summit Ridge Fire Department Logo as a division not as a separate entity without saying it, possibly by depicting it in the background of Side 2 instead of being a standalone picture like the logo on Side 1.

```html
<!DOCTYPE html>
<html lang="en">
<head>
<meta charset="utf-8">
<title>Summit Ridge Business Card</title>
<link href="https://fonts.googleapis.com/css2?family=Montserrat:wght@600;700;800&family=Poppins:wght@400;500;600;700&display=swap" rel="stylesheet">
<style>
  :root {
    --backdrop: #c9c9c9;
    --brand-red: #ff0000;
    --ink-black: #000000;
    --paper-white: #ffffff;
    --text-grey: #333333;
    --card-w: 600px;
    --card-h: 343px;
  }
  html, body {
    margin: 0;
    padding: 0;
    width: 1200px;
    height: 900px;
    overflow: hidden;
    background: var(--backdrop);
  }
  .canvas {
    width: 1200px;
    height: 900px;
    display: flex;
    flex-direction: column;
    align-items: center;
    justify-content: center;
    gap: 44px;
  }
  .card {
    position: relative;
    width: var(--card-w);
    height: var(--card-h);
    border-radius: 26px;
    overflow: hidden;
    box-shadow: 0 8px 18px rgba(0,0,0,0.28);
  }

  /* Side 1 */
  .card--front { background: var(--paper-white); }
  .brand {
    position: absolute;
    top: 44px;
    left: 0;
    right: 0;
    display: flex;
    align-items: center;
    justify-content: center;
    gap: 12px;
  }
  .brand__mark {
    width: 16px;
    height: 16px;
    background: var(--brand-red);
  }
  .brand__name {
    font-family: "Montserrat", sans-serif;
    font-weight: 800;
    font-size: 40px;
    letter-spacing: 2px;
    color: var(--brand-red);
    text-transform: uppercase;
  }
  .services-band {
    position: absolute;
    top: 150px;
    left: 0;
    right: 0;
    height: 140px;
    background: var(--brand-red);
    display: flex;
    flex-direction: column;
    align-items: center;
    justify-content: center;
    gap: 7px;
  }
  .services-band__line {
    font-family: "Montserrat", sans-serif;
    font-weight: 700;
    font-size: 15px;
    letter-spacing: 1px;
    color: var(--paper-white);
    text-transform: uppercase;
  }
  .website {
    position: absolute;
    bottom: 16px;
    left: 0;
    right: 0;
    text-align: center;
    font-family: "Poppins", sans-serif;
    font-size: 17px;
    letter-spacing: 1.5px;
    color: var(--text-grey);
  }
  .website__domain { color: var(--brand-red); }

  /* Side 2 */
  .card--back { background: var(--brand-red); }
  .contact {
    position: absolute;
    top: 58px;
    left: 0;
    right: 0;
    text-align: center;
    color: var(--paper-white);
    font-family: "Poppins", sans-serif;
  }
  .contact__name {
    font-weight: 700;
    font-size: 28px;
    margin: 0;
  }
  .contact__rule {
    width: 70px;
    height: 1px;
    background: var(--paper-white);
    margin: 6px auto 10px;
  }
  .contact__line {
    font-size: 17px;
    font-weight: 500;
    margin: 0;
    line-height: 1.35;
  }
  .field-band {
    position: absolute;
    top: 198px;
    left: 0;
    right: 0;
    height: 92px;
    background: var(--ink-black);
    display: flex;
    flex-direction: column;
    align-items: center;
    justify-content: center;
    gap: 4px;
  }
  .field-band__line {
    font-family: "Montserrat", sans-serif;
    font-weight: 800;
    font-size: 25px;
    letter-spacing: 1px;
    color: var(--paper-white);
    text-transform: uppercase;
  }
  .bullet { color: var(--brand-red); margin: 0 6px; }
  .tagline {
    position: absolute;
    bottom: 16px;
    left: 0;
    right: 0;
    text-align: center;
    font-family: "Poppins", sans-serif;
    font-weight: 600;
    font-size: 16px;
    color: var(--paper-white);
  }
</style>
</head>
<body>
<main class="canvas">
  <section class="card card--front" aria-label="Business card side one">
    <div class="brand">
      <span class="brand__mark"></span>
      <span class="brand__name">Summit Ridge</span>
    </div>
    <div class="services-band">
      <span class="services-band__line">Fire Training &bull; Confined Space Rescue Training</span>
      <span class="services-band__line">Rope Rescue Training &bull; Hazmat Training</span>
      <span class="services-band__line">Incident Command &bull; EMS &bull; Pump Operations Training</span>
    </div>
    <div class="website">www.<span class="website__domain">summitridgeexample</span>.com</div>
  </section>

  <section class="card card--back" aria-label="Business card side two">
    <div class="contact">
      <p class="contact__name">Marcus Hale</p>
      <div class="contact__rule"></div>
      <p class="contact__line">055-987 654 321</p>
      <p class="contact__line">contact@summitridgeexample.com</p>
    </div>
    <div class="field-band">
      <span class="field-band__line">Fire Department<span class="bullet">&bull;</span>Stand-by Rescue</span>
      <span class="field-band__line">Safety<span class="bullet">&bull;</span>EMS<span class="bullet">&bull;</span>Planning</span>
    </div>
    <div class="tagline">Supporting the Emergency Response Community Since 1967</div>
  </section>
</main>
</body>
</html>
```